Tasteful instructions for employees/guests to wash hands

Need an aesthetic visualisation of steps to wash hands.
While we would like to convey the proper steps to wash hands we also don't want to treat our staff/guests like children, rather provide a quick reminder.
Suggested sizes
16″ × 24″
11″ × 14″
A simplified version of these steps:
- Wet your hands with clean, running water (warm or cold), turn off the tap, and apply soap.
- Lather your hands by rubbing them together with the soap. Lather the backs of your hands, between your fingers, and under your nails.
- Scrub your hands for at least 20 seconds.
- Rinse your hands well under clean, running water.
- Dry your hands using a clean towel or air dry them.

```html
<!DOCTYPE html>
<html lang="en">
<head>
<meta charset="UTF-8">
<title>How to Wash Your Hand</title>
<link href="https://fonts.googleapis.com/css2?family=Open+Sans:wght@700;800&family=Raleway:wght@300;400&display=swap" rel="stylesheet">
<style>
  :root {
    --page-bg: #f6f6f6;
    --poster-bg: #ffffff;
    --band-grey: #f1f1f2;
    --ink: #111111;
    --navy: #2f5088;
    --body-ink: #2a2a2a;
    --line: #6b6b6b;
    --art-fill: #dfe2e7;
  }
  * { margin: 0; padding: 0; box-sizing: border-box; }
  html, body {
    width: 1200px; height: 728px; overflow: hidden;
    background: var(--page-bg);
  }
  .poster {
    position: absolute; left: 373px; top: 24px;
    width: 453px; height: 680px;
    background: var(--poster-bg);
    box-shadow: 4px 5px 8px rgba(0,0,0,0.28);
    overflow: hidden;
  }
  .poster-title {
    position: absolute; left: 0; right: 0; top: 28px;
    text-align: center;
    font-family: "Open Sans", sans-serif;
    font-weight: 800;
    font-size: 47px;
    line-height: 48px;
    letter-spacing: 0.07em;
    color: var(--ink);
  }
  .poster-title .accent { color: var(--navy); }
  .band { position: absolute; left: 0; right: 0; }
  .band--grey { background: var(--band-grey); }
  .step-path { position: absolute; inset: 0; }
  .step-art {
    position: absolute; width: 64px; height: 70px;
    background: var(--art-fill); border-radius: 6px;
  }
  .step-text {
    position: absolute;
    transform: translateY(-50%);
    font-family: "Raleway", sans-serif;
    font-weight: 400;
    font-size: 11.5px;
    line-height: 14px;
    letter-spacing: 0.13em;
    color: var(--body-ink);
  }
  .step-text--odd { left: 260px; }
  .step-text--even { left: 283px; }
  .step-num {
    font-family: "Raleway", sans-serif; font-size: 15px; fill: #fff;
  }
</style>
</head>
<body>
  <main class="poster">
    <h1 class="poster-title">HOW TO <span class="accent">WASH</span><br>YOUR <span class="accent">HAND</span></h1>

    <div class="band band--grey" style="top:158px;height:81px"></div>
    <div class="band band--grey" style="top:316px;height:81px"></div>
    <div class="band band--grey" style="top:481px;height:81px"></div>

    <svg class="step-path" width="453" height="680" viewBox="0 0 453 680">
      <polyline points="107,203 135,282 107,358 135,437 107,520 130,599" fill="none" stroke="var(--line)" stroke-width="0.8"/>
      <g fill="var(--navy)">
        <circle cx="107" cy="203" r="13"/>
        <circle cx="135" cy="282" r="13"/>
        <circle cx="107" cy="358" r="13"/>
        <circle cx="135" cy="437" r="13"/>
        <circle cx="107" cy="520" r="13"/>
        <circle cx="130" cy="599" r="13"/>
      </g>
      <g class="step-num" text-anchor="middle">
        <text x="107" y="208">1</text>
        <text x="135" y="287">2</text>
        <text x="107" y="363">3</text>
        <text x="135" y="442">4</text>
        <text x="107" y="525">5</text>
        <text x="130" y="604">6</text>
      </g>
    </svg>

    <div class="step-art" role="img" aria-label="Line drawing of hands under running tap water" style="left:29px;top:166px"></div>
    <div class="step-art" role="img" aria-label="Line drawing of hands applying soap with bubbles" style="left:155px;top:250px;height:60px"></div>
    <div class="step-art" role="img" aria-label="Line drawing of hands rubbing together with lather" style="left:29px;top:325px"></div>
    <div class="step-art" role="img" aria-label="Line drawing of hands lathering backs and between fingers" style="left:155px;top:403px"></div>
    <div class="step-art" role="img" aria-label="Line drawing of hands rinsing under running water" style="left:29px;top:488px"></div>
    <div class="step-art" role="img" aria-label="Line drawing of hands drying with a towel" style="left:155px;top:573px;height:84px"></div>

    <p class="step-text step-text--odd" style="top:203px">Wet your hands<br>with clean,<br>running water<br>(warm or cold)</p>
    <p class="step-text step-text--even" style="top:282px">turn off the tap<br>and apply soap</p>
    <p class="step-text step-text--odd" style="top:358px">Lather your hands<br>by rubbing them<br>together with the soap</p>
    <p class="step-text step-text--even" style="top:437px">Lather the backs<br>of your hands,<br>between your fingers<br>and under your nails</p>
    <p class="step-text step-text--odd" style="top:520px">Rinse your hands<br>well under clean,<br>running water</p>
    <p class="step-text step-text--even" style="top:599px">Dry your hands<br>using a clean towel<br>or air dry them</p>
  </main>
</body>
</html>
```